A website for a Maltese Law Firm

Our law firm needs a website to further its business. The site should have a simple yet effective design. We would need the following sections: About us, Practice Areas, About Malta, Contact. These should be further split as follows:

About us: Our firm, Our values, What others say, Offices

Practice Areas: Crimimal, Citizenship & Residence, Sovereign Patron Pathway, Criminal Defence, Civil Litigation, Arbitration and ADR, Commercial and Corporate, Media Law.

About Malta: just one section.

Contact: Just one section

We would also need a news feed at the front of the site to include latest news regarding our cases.

At the bottom we need a section for our Terms and a Privacy Statement.

Our logo is being attached.

Target Market(s)

All clients looking for legal assistance in Malta

Industry/Entity Type

Legal

Coding

Coded - Design and coding required

Number of Pages Required

1 page

Requirements
Must have
• It must be simple yet striking.

```html
<!DOCTYPE html>
<html lang="en">
<head>
<meta charset="utf-8">
<title>Aquilina &amp; Sultana Advocates</title>
<link rel="stylesheet" href="https://fonts.googleapis.com/css2?family=Cinzel:wght@400;700&family=Montserrat:wght@400;600&display=swap">
<style>
:root{
  --ink:#222;
  --text:#666;
  --dark:#2f2f2f;
  --footer:#333;
  --line:#cfcfcf;
  --band:#efefef;
  --white:#fff;
  --news-bg:#e6eaf0;
}
*{margin:0;padding:0;box-sizing:border-box}
html,body{width:1200px;height:2397px;overflow:hidden}
body{position:relative;background:var(--white);font-family:"Montserrat",sans-serif;color:var(--text)}
.abs{position:absolute}
.serif{font-family:"Cinzel",serif}

/* top bar */
.topbar{left:0;top:0;width:1200px;height:35px;border-bottom:1px solid #e2e2e2}
.social{left:99px;top:0;height:35px;display:flex}
.social span{width:39px;height:35px;border-left:1px solid #e2e2e2;display:flex;align-items:center;justify-content:center}
.social span:last-child{border-right:1px solid #e2e2e2}
.social i{width:9px;height:9px;border-radius:50%;background:#555;display:block}
.callbar{left:880px;top:0;width:221px;height:35px;background:var(--dark);color:var(--white);font-size:12px;letter-spacing:1px;display:flex;align-items:center;gap:10px;padding-left:16px}

/* header */
.header{left:0;top:35px;width:1200px;height:77px;border-bottom:2px solid var(--dark)}
.logo{left:99px;top:20px;font-family:"Cinzel",serif;font-size:28px;color:var(--ink);letter-spacing:.5px}
.nav{right:99px;top:28px;display:flex;gap:36px;font-family:"Cinzel",serif;font-size:14px;color:var(--ink)}
.nav .active{border-bottom:2px solid var(--ink);border-top:1px solid var(--ink);padding:3px 4px}
.nav a{padding:4px 0}

/* hero */
.hero{left:0;top:112px;width:1200px;height:466px;background:linear-gradient(120deg,#6d6661 0%,#b8b0a8 35%,#d9d2c8 60%,#8f8780 100%)}
.hero-title{left:99px;top:195px;font-family:"Cinzel",serif;font-size:27px;line-height:34px;color:var(--white);letter-spacing:1px}
.hero-btn{left:99px;top:276px;padding:8px 10px;border:1px solid var(--white);color:var(--white);font-family:"Cinzel",serif;font-size:12px;letter-spacing:.5px}
.arrow{top:196px}

/* section headings */
.heading{font-family:"Cinzel",serif;font-size:25px;color:#555;letter-spacing:1px;white-space:nowrap}
.heading b{font-weight:400;color:var(--ink);border-bottom:2px solid var(--ink);padding-bottom:2px}
.heading b::before{content:"";display:inline-block}

/* about */
.about-para{left:99px;top:690px;width:590px;font-size:13px;line-height:25.5px;color:var(--text)}
.btn-dark{left:99px;top:857px;width:134px;height:38px;background:var(--dark);color:var(--white);font-family:"Cinzel",serif;font-size:13px;display:flex;align-items:center;justify-content:center}
.icon-box{width:96px;height:94px;border:1px solid #bbb;display:flex;align-items:center;justify-content:center;background:var(--white)}
.value h3{font-family:"Cinzel",serif;font-weight:400;font-size:17px;color:var(--ink);margin-bottom:6px}
.value p{font-size:12px;line-height:19px;width:240px}

/* practice */
.practice{left:0;top:946px;width:1200px;height:350px;background:linear-gradient(90deg,var(--band) 55%,#e8e8e8 100%)}
.area{width:152px;text-align:center}
.area .icon-box{width:152px;height:97px}
.area p{font-family:"Cinzel",serif;font-size:13px;color:var(--ink);line-height:15px;height:40px;display:flex;align-items:center;justify-content:center;border-bottom:2px solid #bbb;margin-top:8px;padding-bottom:4px}
.dots{left:583px;top:1242px;display:flex;gap:4px}
.dots i{width:9px;height:9px;border:1px solid #888;border-radius:50%;display:block}
.dots i:first-child{background:#888;box-shadow:inset 0 0 0 2px var(--band)}

/* malta */
.frame{left:99px;top:1401px;width:422px;height:245px;border:1px solid #ccc}
.malta-photo{left:117px;top:1419px;width:420px;height:248px;background:linear-gradient(180deg,#7b9bc6 0%,#a9b7cf 40%,#d39a4c 58%,#6a7fb0 72%,#8fa0cf 100%)}
.malta-text{left:566px;top:1402px;width:535px;font-size:13px;line-height:25.5px}
.bullets{left:566px;top:1566px;width:540px;font-size:12.5px;font-weight:600;color:var(--ink);line-height:17px}
.bullets li{list-style:none;display:flex;gap:12px;margin-bottom:15px}

/* news */
.news{left:0;top:1721px;width:1200px;height:455px;background:linear-gradient(90deg,#eef0f4 0%,var(--news-bg) 70%,#dfe4eb 100%)}
.news-photo{width:479px;height:173px}
.date{width:60px;height:60px;background:var(--dark);color:var(--white);text-align:center;font-size:14px;line-height:20px;padding-top:9px}
.date b{font-size:19px;display:block}
.news-text{width:479px;font-size:12.5px;line-height:22px}
.btn-line{width:126px;height:36px;border:1px solid var(--dark);font-family:"Cinzel",serif;font-size:13px;color:var(--ink);display:flex;align-items:center;justify-content:center}

/* footer */
.footer{left:0;top:2176px;width:1200px;height:221px;background:var(--footer);color:#ddd}
.f-logo{left:121px;top:2255px;font-family:"Cinzel",serif;font-size:23px;color:var(--white)}
.copy{left:99px;top:2312px;font-size:11px;color:#ccc}
.f-head{font-family:"Cinzel",serif;font-size:16px;color:var(--white);letter-spacing:1px;border-bottom:1px solid #666;padding-bottom:6px}
.f-link{font-size:11px;color:#ccc;display:flex;align-items:center;gap:8px}
.f-link::before{content:"";width:6px;height:6px;border:1px solid #aaa;transform:rotate(45deg)}
.f-social{left:594px;top:2344px;display:flex;gap:14px}
.f-social i{width:9px;height:9px;border-radius:50%;background:var(--white);display:block}
.input{left:799px;top:2268px;width:256px;height:33px;background:#4a4a4a;font-size:11px;font-style:italic;color:#aaa;padding:10px 14px}
.send{left:1055px;top:2268px;width:46px;height:33px;background:#e5e5e5;display:flex;align-items:center;justify-content:center}
.contact-line{font-size:11px;color:#ddd;display:flex;align-items:center;gap:8px}
</style>
</head>
<body>

<div class="abs topbar"></div>
<div class="abs social"><span><i></i></span><span><i></i></span><span><i></i></span><span><i></i></span></div>
<div class="abs callbar">
  <svg width="14" height="14" viewBox="0 0 24 24"><path d="M6.6 10.8a15 15 0 006.6 6.6l2.2-2.2c.3-.3.7-.4 1-.2 1.1.4 2.3.6 3.6.6.6 0 1 .4 1 1V20c0 .6-.4 1-1 1A17 17 0 013 4c0-.6.4-1 1-1h3.5c.6 0 1 .4 1 1 0 1.3.2 2.5.6 3.6.1.3 0 .7-.2 1z" fill="#fff"/></svg>
  CALL US : (356) 2000 4188
</div>

<header class="abs header">
  <div class="abs logo">Aquilina &amp; Sultana</div>
  <nav class="abs nav"><a class="active">Home</a><a>About us</a><a>Practice Areas</a><a>About Malta</a><a>Contact</a></nav>
</header>

<section class="abs hero" role="img" aria-label="Photograph of a lawyer's hands signing documents with a pen at a desk">
  <svg class="abs arrow" style="left:26px" width="44" height="46" viewBox="0 0 44 46"><path d="M16 2H4a2 2 0 00-2 2v38a2 2 0 002 2h12" fill="none" stroke="#333" stroke-width="2.5"/><path d="M40 23H12M20 14l-9 9 9 9" fill="none" stroke="#333" stroke-width="2.5"/></svg>
  <svg class="abs arrow" style="left:1130px" width="44" height="46" viewBox="0 0 44 46"><path d="M28 2h12a2 2 0 012 2v38a2 2 0 01-2 2H28" fill="none" stroke="#333" stroke-width="2.5"/><path d="M4 23h28M24 14l9 9-9 9" fill="none" stroke="#333" stroke-width="2.5"/></svg>
  <h1 class="abs hero-title" style="font-weight:400">The Greatest &amp; Stongest<br>Firm You Can Trust</h1>
  <div class="abs hero-btn">Request A Free Consultant</div>
</section>

<!-- About -->
<h2 class="abs heading" style="left:99px;top:640px;font-weight:400">About <b>Aquilina &amp; Sultana</b></h2>
<p class="abs about-para">Lorem ipsum dolor sit amet, consectetuer adipiscing elit, sed diam nonummy nibh euismod tincidunt ut laoreet dolore magna aliquam erat volutpat. Ut wisi enim ad minim veniam, quis nostrud exerci tation ullamcorper suscipit lobortis nisl ut aliquip ex ea commodo consequat. Duis autem vel eum iriure dolor in hendrerit in vulputate velit esse molestie consequat, vel illum dolore eu feugiat nulla facilisis at vero eros et accumsan et iusto odio dignissim qui blandit praesent luptatum &nbsp;te feugait nulla facilisi.</p>
<div class="abs btn-dark">Read More</div>

<div class="abs icon-box" style="left:748px;top:663px">
  <svg width="60" height="40" viewBox="0 0 60 40"><path d="M2 12l12-8 10 4 8-4 14 2 12 8-8 10-4-2-12 12c-2 2-5 1-5-1-2 1-5 0-5-2-2 1-5-1-4-3-2 0-4-2-3-4l-5-4z" fill="#333"/><path d="M22 14l8-4 10 10" fill="none" stroke="#fff" stroke-width="2"/></svg>
</div>
<div class="abs value" style="left:863px;top:664px"><h3>Our Values</h3><p>Artis nisl ut aliquip ex ea commodoll eros et accumsan o digniss qui nulla facilisi...[+]</p></div>

<div class="abs icon-box" style="left:748px;top:791px">
  <svg width="60" height="52" viewBox="0 0 60 52"><path d="M30 2L4 14h52z" fill="#333"/><rect x="4" y="16" width="52" height="4" fill="#333"/><rect x="9" y="23" width="6" height="19" fill="#333"/><rect x="21" y="23" width="6" height="19" fill="#333"/><rect x="33" y="23" width="6" height="19" fill="#333"/><rect x="45" y="23" width="6" height="19" fill="#333"/><rect x="2" y="44" width="56" height="5" fill="#333"/></svg>
</div>
<div class="abs value" style="left:863px;top:795px"><h3>Our Firm</h3><p>Artis nisl ut aliquip ex ea commodoll eros et accumsan o digniss qui nulla facilisi...[+]</p></div>

<!-- Practice Areas -->
<section class="abs practice"></section>
<h2 class="abs heading" style="left:499px;top:988px;font-weight:400">Practice <b>Areas</b></h2>

<div class="abs area" style="left:99px;top:1063px">
  <div class="icon-box"><svg width="60" height="46" viewBox="0 0 60 46"><circle cx="18" cy="28" r="12" fill="none" stroke="#333" stroke-width="5"/><circle cx="42" cy="20" r="12" fill="none" stroke="#333" stroke-width="5"/><rect x="24" y="6" width="12" height="6" fill="#333"/></svg></div>
  <p>Criminal Law</p>
</div>
<div class="abs area" style="left:312px;top:1063px">
  <div class="icon-box"><svg width="56" height="46" viewBox="0 0 56 46"><path d="M28 2L2 24h7v20h14V32h10v12h14V24h7z" fill="#333"/></svg></div>
  <p>Citizenship &amp;<br>Residence</p>
</div>
<div class="abs area" style="left:524px;top:1063px">
  <div class="icon-box"><svg width="54" height="52" viewBox="0 0 54 52"><circle cx="24" cy="16" r="12" fill="#333"/><path d="M4 50c0-14 9-22 20-22s20 8 20 22z" fill="#333"/><path d="M40 34l10 10-4 1 3 5-2 1-3-5-3 3z" fill="#333"/></svg></div>
  <p>Sovereign Patron<br>Pathway</p>
</div>
<div class="abs area" style="left:737px;top:1063px">
  <div class="icon-box"><svg width="56" height="50" viewBox="0 0 56 50"><rect x="14" y="6" width="22" height="12" transform="rotate(40 25 12)" fill="#333"/><rect x="26" y="18" width="26" height="5" transform="rotate(40 26 20)" fill="#333"/><rect x="4" y="40" width="30" height="7" fill="#333"/></svg></div>
  <p>Civil<br>Litigation</p>
</div>
<div class="abs area" style="left:949px;top:1063px">
  <div class="icon-box"><svg width="56" height="50" viewBox="0 0 56 50"><rect x="10" y="2" width="36" height="32" fill="#333"/><rect x="16" y="8" width="24" height="20" fill="#fff"/><rect x="22" y="16" width="12" height="12" fill="#333"/><rect x="4" y="38" width="48" height="4" fill="#333"/><rect x="4" y="45" width="48" height="4" fill="#333"/></svg></div>
  <p>Arbitration<br>and ADR</p>
</div>
<div class="abs dots"><i></i><i></i><i></i></div>

<!-- About Malta -->
<h2 class="abs heading" style="left:522px;top:1341px;font-weight:400">About <b>Malta</b></h2>
<div class="abs frame"></div>
<div class="abs malta-photo" role="img" aria-label="Photograph of the illuminated Valletta skyline across the harbour at dusk"></div>
<p class="abs malta-text">Aeuismod tincidunt ut laoreet dolore magna aliquam erat volutpat. Ut wisi enim ad minim veniam, quis nostrud exerci tation ullamcorper suscipit lobortis nisl ut aliquip ex ea commodo consequat. Duis autem vel eum iriure dolor in hendrerit in vulputate velit esse molestie consequat, vel illum dolore eu feugiat nulla facilisis at vero eros et accumsan et iusto odio dignissim qui blandit praesent luptatum &nbsp;te feugait nulla facilisi.</p>
<ul class="abs bullets">
  <li><svg width="14" height="14" viewBox="0 0 14 14"><path d="M1 3h7l5 4-5 4H1z" fill="none" stroke="#333" stroke-width="1.3"/></svg><span>Duis autem vel eum iriure dolor in hendrerit in vulputate vl conseqt,molestie consequat vel illum dolore.</span></li>
  <li><svg width="14" height="14" viewBox="0 0 14 14"><path d="M1 3h7l5 4-5 4H1z" fill="none" stroke="#333" stroke-width="1.3"/></svg><span>Ut wisi enim ad minim veniam, qui nostrud exeullamcorper suscipit lobortis .</span></li>
  <li><svg width="14" height="14" viewBox="0 0 14 14"><path d="M1 3h7l5 4-5 4H1z" fill="none" stroke="#333" stroke-width="1.3"/></svg><span>Aulputate velit esse molestie consequat, vel illum dolore eu feugiat.</span></li>
</ul>

<!-- Latest News -->
<section class="abs news"></section>
<h2 class="abs heading" style="left:515px;top:1758px;font-weight:400">Latest <b>News</b></h2>

<div class="abs news-photo" style="left:99px;top:1834px;background:linear-gradient(135deg,#2b2b2e 0%,#55555a 50%,#2e2a28 100%)" role="img" aria-label="Photograph of a man reading documents at a desk"></div>
<div class="abs date" style="left:99px;top:1947px"><b>08</b>JUNE</div>
<p class="abs news-text" style="left:99px;top:2024px">lobortis nisl ut aliquip ex ea commodo consequat. Duis autem vel eum iriure dolor in hendrerit inilore eu feugiat nulla facilisis at vero..</p>
<div class="abs btn-line" style="left:99px;top:2089px">Read More</div>

<div class="abs news-photo" style="left:622px;top:1834px;background:linear-gradient(135deg,#f2f2f2 0%,#d9c7a8 40%,#7a3a1c 65%,#d8c9b4 100%)" role="img" aria-label="Photograph of a wooden gavel resting on an open book"></div>
<div class="abs date" style="left:622px;top:1947px"><b>08</b>JUNE</div>
<p class="abs news-text" style="left:622px;top:2024px">lobortis nisl ut aliquip ex ea commodo consequat. Duis autem vel eum iriure dolor in hendrerit in vulpue molestie ct, velo..</p>
<div class="abs btn-line" style="left:622px;top:2089px">Read More</div>

<!-- Footer -->
<footer class="abs footer"></footer>
<div class="abs f-logo">Aquilina &amp; Sultana</div>
<div class="abs copy">Copyright © 2016 ASadvocates. All rights reserved.</div>

<div class="abs f-head" style="left:465px;top:2218px">Navigation</div>
<div class="abs f-link" style="left:463px;top:2265px">Home</div>
<div class="abs f-link" style="left:590px;top:2265px">About Malta</div>
<div class="abs f-link" style="left:463px;top:2304px">About us</div>
<div class="abs f-link" style="left:590px;top:2304px">Contact Us</div>
<div class="abs f-link" style="left:463px;top:2344px">Practice Areas</div>
<div class="abs f-social"><i></i><i></i><i></i><i></i></div>

<div class="abs f-head" style="left:799px;top:2218px">Newsletter</div>
<div class="abs input">Enter Your Email</div>
<div class="abs send"><svg width="20" height="18" viewBox="0 0 20 18"><path d="M1 8L19 1 15 17 9 12 5 16V11z" fill="none" stroke="#333" stroke-width="1.4"/><path d="M5 11L19 1" stroke="#333" stroke-width="1.2"/></svg></div>
<div class="abs contact-line" style="left:806px;top:2318px"><svg width="10" height="13" viewBox="0 0 10 13"><path d="M5 0a5 5 0 00-5 5c0 4 5 8 5 8s5-4 5-8a5 5 0 00-5-5z" fill="#fff"/><circle cx="5" cy="5" r="2" fill="#333"/></svg>18 Triq il-Merill, Ħal Qormi</div>
<div class="abs contact-line" style="left:806px;top:2347px"><svg width="12" height="12" viewBox="0 0 24 24"><path d="M6.6 10.8a15 15 0 006.6 6.6l2.2-2.2c.3-.3.7-.4 1-.2 1.1.4 2.3.6 3.6.6.6 0 1 .4 1 1V20c0 .6-.4 1-1 1A17 17 0 013 4c0-.6.4-1 1-1h3.5c.6 0 1 .4 1 1 0 1.3.2 2.5.6 3.6.1.3 0 .7-.2 1z" fill="#fff"/></svg>(356) 2000 4188</div>
<div class="abs contact-line" style="left:944px;top:2347px"><svg width="14" height="10" viewBox="0 0 14 10"><rect width="14" height="10" fill="#fff"/><path d="M0 0l7 6 7-6" fill="none" stroke="#333" stroke-width="1.2"/></svg>info@asadvocates.com</div>

</body>
</html>
```